Wandering Rooms Stationary Set

Wandering Rooms is a bespoke interior design firm set to provide services to VIP clients with elegance and minimalism is the main theme for our stationary set. We require a full stationary set covering A4 letterhead, A4 & A3 envelopes, business cards, USB's, CDs, email signature and any other item the designer sees fit. logo is already designed and finalized, and we require the designer to use it as is without modifying the logo.

Address to be used on letterhead / business cards ...etc shall be as follows:

Phone : +971 2 518 2047
P.O. Box : 309186
Address: Block C&D, Bldg. 47, Court 12, Abu Dhabi, United Arab Emirates
Website: www.wanderingrooms-example.com

Target Market(s)

VIP Clients

Industry/Entity Type

Interior Design

Font styles to use
Other font styles liked:
• something to be unique

Colors

Designer to choose colors to be used in the design.

Requirements
Must have
• Elegant, minimalistic
Nice to have
• Simple yet elegant design having a sharp yet clean cut format
Should not have
• No additional colours, just colours that are used in the logo (silver, black or gold)

```html
<!DOCTYPE html>
<html lang="en">
<head>
<meta charset="utf-8">
<title>Wandering Rooms – Business Cards</title>
<link href="https://fonts.googleapis.com/css2?family=Cormorant+Garamond:wght@400;500&family=Great+Vibes&display=swap" rel="stylesheet">
<style>
  :root {
    --backdrop: #1c1c1d;
    --card: #2a2a2b;
    --card-edge: #232324;
    --gold: #c9a24e;
    --silver: #a9a9ab;
    --silver-light: #d2d2d4;
    --text-grey: #8e8e90;
  }
  * { box-sizing: border-box; margin: 0; padding: 0; }
  html, body {
    width: 1200px; height: 800px; overflow: hidden;
    background: var(--backdrop);
    font-family: "Cormorant Garamond", Georgia, serif;
  }
  .card-stack {
    position: absolute; left: 340px; top: 83px;
    display: flex; flex-direction: column; gap: 40px;
  }
  .card {
    position: relative; width: 520px; height: 297px;
    background: var(--card);
    border: 1px solid var(--card-edge);
    box-shadow: 0 12px 30px rgba(0,0,0,.45);
  }
  /* Front */
  .card--front { display: flex; align-items: center; justify-content: center; }
  .wordmark { text-align: center; line-height: 1; }
  .wordmark__name {
    font-size: 46px; font-weight: 400; letter-spacing: 1px;
    color: var(--silver);
  }
  .wordmark__rule { display: block; width: 46px; height: 1px; margin: 12px auto 0; background: var(--silver); }

  /* Back */
  .card--back .wordmark { position: absolute; left: 38px; top: 52px; text-align: left; }
  .card--back .wordmark__name { font-size: 34px; color: var(--gold); }
  .holder { position: absolute; right: 36px; top: 102px; text-align: right; }
  .holder__name { font-family: "Great Vibes", cursive; font-size: 30px; color: var(--gold); line-height: 1; }
  .holder__title { font-size: 14px; color: var(--silver-light); margin-top: 2px; }
  .holder__rule { width: 150px; height: 1px; background: var(--gold); margin: 6px 0 0 auto; }
  .web { position: absolute; right: 36px; top: 178px; font-size: 12.5px; color: var(--silver); }
  .label { color: var(--gold); font-weight: 500; margin-right: 4px; }
  .address {
    position: absolute; left: 38px; top: 196px;
    font-size: 12px; line-height: 1.35; color: var(--text-grey);
  }
  .contact-rule { position: absolute; left: 38px; right: 36px; top: 252px; height: 1px; background: var(--gold); opacity: .8; }
  .contact-row {
    position: absolute; left: 38px; right: 36px; top: 260px;
    display: flex; gap: 38px; font-size: 12.5px; color: var(--silver);
  }
</style>
</head>
<body>
  <main class="card-stack">
    <section class="card card--front" aria-label="Business card front">
      <div class="wordmark">
        <div class="wordmark__name">Wandering Rooms</div>
        <span class="wordmark__rule"></span>
      </div>
    </section>

    <section class="card card--back" aria-label="Business card back">
      <div class="wordmark">
        <div class="wordmark__name">Wandering Rooms</div>
      </div>

      <div class="holder">
        <div class="holder__name">Daniel Hartley</div>
        <div class="holder__title">President</div>
        <div class="holder__rule"></div>
      </div>
      <div class="web"><span class="label">W :</span>www.wanderingrooms-example.com</div>

      <address class="address" style="font-style:normal">
        P.O. Box : 309186<br>
        Block C&amp;D, Bldg. 47, Court 12<br>
        Abu Dhabi, United Arab Emirates
      </address>
      <div class="contact-rule"></div>
      <div class="contact-row">
        <span><span class="label">P :</span>+971 2 518 2047</span>
        <span><span class="label">E :</span>info@wanderingrooms-example.com</span>
      </div>
    </section>
  </main>
</body>
</html>
```